US Recruiting Firm Needs Dynamic Tri-Fold Brochure

Need tri-fold professional brochure for HR recruiting and consulting firm based in the US.

Target Market(s)

Clients seeking administrative and human resources talent

Industry/Entity Type

Recruitment

Font styles to use
Sans Serif

Requirements
Should not have
• No weird shapes
• No heavy geometric shapes -- I prefer curvy lines
• Not a dark brochure

```html
<!DOCTYPE html>
<html lang="en">
<head>
<meta charset="utf-8">
<title>Recruiting Partner Tri-Fold Brochure – Inside Spread</title>
<link rel="stylesheet" href="https://fonts.googleapis.com/css2?family=Montserrat:ital,wght@0,300;0,400;0,600;0,800;1,700&family=Lato:wght@400;700&display=swap">
<style>
  :root {
    --navy: #1f3a66;
    --navy-deep: #10264a;
    --orange: #f26a1b;
    --purple: #8a2a8c;
    --lime: #a8cc2c;
    --paper: #f4f4f5;
    --paper-shade: #e6e6e8;
    --ink: #2c3347;
    --backdrop: #d9dadd;
    --white: #ffffff;
  }
  * { box-sizing: border-box; margin: 0; padding: 0; }
  html, body {
    width: 1200px; height: 800px; overflow: hidden;
    background: var(--backdrop);
    font-family: "Lato", sans-serif;
    color: var(--ink);
  }
  .brochure {
    position: absolute; left: 60px; top: 20px;
    width: 1080px; height: 760px;
    display: flex;
    background: var(--paper);
    box-shadow: 0 6px 24px rgba(0,0,0,.18);
    overflow: hidden;
  }
  .panel {
    position: relative; width: 360px; height: 100%;
    padding: 38px 30px 0;
  }
  .panel + .panel { border-left: 1px solid rgba(0,0,0,.08); }

  .panel-photo {
    position: absolute; inset: 0 0 60px 0;
    background: radial-gradient(ellipse at 70% 30%, #d2d3d6 0%, #e9e9eb 45%, var(--paper) 75%);
    z-index: 0;
  }
  .panel > *:not(.panel-photo):not(.footer-band) { position: relative; z-index: 1; }

  .heading {
    font-family: "Montserrat", sans-serif;
    font-size: 21px; line-height: 1.15;
    color: var(--navy); font-weight: 300;
    text-transform: uppercase;
  }
  .heading strong { color: var(--orange); font-weight: 800; }
  .rule {
    height: 2px; width: 88%;
    background: var(--purple);
    margin: 8px 0 10px;
  }
  .body-text {
    font-size: 11.5px; line-height: 1.45;
    color: var(--ink);
  }
  .tagline {
    font-family: "Montserrat", sans-serif;
    font-weight: 700; font-style: italic;
    color: var(--navy); font-size: 12.5px;
    margin: 10px 0 22px;
  }
  .section-gap { margin-top: 20px; }

  .tick-list { list-style: none; font-size: 12.5px; line-height: 1.45; color: var(--ink); }
  .tick-list li { position: relative; padding-left: 20px; }
  .tick-list li::before {
    content: ""; position: absolute; left: 3px; top: 3px;
    width: 5px; height: 10px;
    border-right: 2px solid var(--orange);
    border-bottom: 2px solid var(--orange);
    transform: rotate(40deg);
  }
  .tick-list.compact { font-size: 11.5px; line-height: 1.5; }

  .label {
    font-family: "Montserrat", sans-serif;
    color: var(--purple); font-weight: 600;
    font-size: 13px; text-transform: uppercase;
    margin-top: 8px;
  }
  .subhead {
    font-family: "Montserrat", sans-serif;
    font-weight: 600; font-style: italic;
    font-size: 11px; color: var(--navy-deep);
  }

  .illustration {
    position: absolute !important; left: 40px; right: 40px; bottom: 78px;
    height: 110px; border-radius: 14px;
    background: linear-gradient(135deg, #f7c44a 0%, #e85c3a 45%, #3b4a6b 100%);
    opacity: .85;
  }

  .talent-band {
    position: absolute; left: 360px; top: 430px;
    width: 720px; height: 262px;
    background: linear-gradient(120deg, var(--navy-deep) 0%, #1b4570 55%, #2c6a93 100%);
    z-index: 2;
    color: var(--white);
    padding: 20px 30px;
  }
  .talent-band .band-title {
    font-family: "Montserrat", sans-serif;
    font-weight: 600; font-size: 16px; line-height: 1.25;
    text-transform: uppercase; letter-spacing: .3px;
  }
  .talent-columns { display: flex; margin-top: 12px; }
  .talent-columns .tick-list { color: var(--white); font-size: 11.5px; line-height: 1.4; width: 360px; }
  .talent-columns .tick-list + .tick-list { padding-left: 0; }

  .footer-band {
    position: absolute; left: 0; right: 0; bottom: 0;
    height: 60px; background: var(--lime);
    border-top: 4px solid var(--purple);
    display: flex; align-items: center; justify-content: center;
    font-family: "Montserrat", sans-serif;
    font-weight: 600; font-size: 17px; color: var(--navy-deep);
    z-index: 3;
  }
</style>
</head>
<body>
<main class="brochure">

  <section class="panel panel-partner">
    <div class="panel-photo" role="img" aria-label="Soft grayscale portrait photo of a smiling professional"></div>
    <h2 class="heading">A Trusted<br><strong>Recruiting Partner</strong></h2>
    <div class="rule"></div>
    <p class="body-text">We have over 20 years of recruiting and human resources experience. Our recruiters have the expertise, insights, and passion to bring value-added recruiting services to your company.</p>
    <p class="tagline">We have a track record of excellence.</p>

    <h2 class="heading">Why <strong>Choose Us?</strong></h2>
    <div class="rule"></div>
    <ul class="tick-list">
      <li>We are HR experts dedicated to recruiting HR professionals</li>
      <li>Highly Qualified talent network</li>
      <li>Comprehensive pre-screening</li>
      <li>Simplified recruiting process</li>
      <li>Reasonable placement fees</li>
      <li>90-Day replacement guarantee</li>
    </ul>

    <h2 class="heading section-gap">Our <strong>Mission</strong></h2>
    <div class="rule"></div>
    <p class="body-text">We have a two-fold mission. We help companies hire the best HR staff to help meet organizational goals and cultivate a highly engaged, productive workforce. We also help HR talent find fulfilling work and careers with awesome companies.</p>

    <div class="illustration" role="img" aria-label="Flat illustration of office icons: target on a monitor, trophy, charts, phone and briefcase"></div>
    <footer class="footer-band">www.pinecreststaffing.com</footer>
  </section>

  <section class="panel panel-hr">
    <div class="panel-photo" role="img" aria-label="Faint grayscale photo of an HR professional"></div>
    <h2 class="heading">Human <strong>Resources:</strong></h2>
    <p class="subhead">One of the Most Critical Function in a Company</p>
    <div class="rule"></div>
    <p class="label">Question</p>
    <p class="body-text">How do companies attract and retain the best employees?</p>
    <p class="label">Answer</p>
    <p class="body-text">They do so by hiring the best human resources staff.</p>
    <p class="body-text" style="margin-top:8px">Human resources professionals are no longer paper pushers. They are now true business partners. They provide critical services that have direct impact on your company's bottom line.</p>
    <p class="body-text" style="margin-top:8px">HR can help or hinder your company's progress. By hiring the best HR talent, your company is positioned and destined for success. Whether you need a HR Coordinator to assist with organizing and tracking projects, a HR Manager to be an advisory resource and provide both strategic and tactical solutions for managers and employees, or an executive to direct and lead the HR function, we can help.</p>
    <footer class="footer-band">www.pinecreststaffing.com</footer>
  </section>

  <section class="panel panel-services">
    <h2 class="heading">We Provide Customized<br>Recruiting and <strong>Consulting<br>Services.</strong></h2>
    <div class="rule"></div>
    <ul class="tick-list compact">
      <li>Working with hiring managers on requisitions</li>
      <li>Position &amp; Candidate Profiling</li>
      <li>Sourcing resumes</li>
      <li>Writing and placing job postings</li>
      <li>Screening and interviewing candidates</li>
      <li>Shortlisting Candidates</li>
      <li>Candidate Assessment</li>
      <li>Coordinating Interviews &amp; Debriefing</li>
      <li>Candidate Dispositioning &amp; Updates</li>
      <li>Applicant Tracking</li>
      <li>Job Offers &amp; Salary Negotiation</li>
      <li>Start Date Coordination &amp; Offer Letter</li>
      <li>Onboarding Process / New Hire Paperwork</li>
      <li>New Hire Follow-up &amp; Check-In Surveys</li>
    </ul>
    <footer class="footer-band">www.pinecreststaffing.com</footer>
  </section>

  <section class="talent-band" role="img" aria-label="Dark blue toned photo of a team working in an office">
    <h3 class="band-title">We offer stellar HR talent from entry to executive level.<br>Positions that we fill include:</h3>
    <div class="talent-columns">
      <ul class="tick-list">
        <li>HR Assistant</li>
        <li>HR Coordinator</li>
        <li>HR Specialist</li>
        <li>HR Generalist</li>
        <li>HR Consultant</li>
        <li>HR Manager</li>
        <li>Employee Relations Specialist</li>
        <li>Employee Relations Manager</li>
        <li>Talent Acquisition Consultant</li>
      </ul>
      <ul class="tick-list">
        <li>Talent Acquisition Specialist</li>
        <li>Recruiter</li>
        <li>Recruiter/HR Generalist</li>
        <li>Benefits Coordinator</li>
        <li>Benefits Specialist</li>
        <li>Compensation Specialist</li>
        <li>Compensation Manager</li>
        <li>Training Specialist</li>
        <li>Learning &amp; Development Consultant</li>
        <li>Diversity and Inclusion Consultant</li>
      </ul>
    </div>
  </section>

</main>
</body>
</html>
```